A new presentation to our clients

we are a Real Estate agency, our website is www.lumibrasa.com and it’s time to have a new, fashion and remarcable Business Card. we want to differentiate ourselves from other companies so we want a business card that differentiates us. we want the business card to impact our customers. in the competitive market that we have today, we have to be different and it is this difference that we seek

Target Market(s)

Real Estate Clients

Contact Information for Business Card

We search a totaly diferent card from the usual

Font styles to use
Sans Serif

Colors
e34197

Requirements
Must have
• Logo, adress, phone contact, e-mail, photo, and our website
Nice to have
• We would like to see a modern business card
Should not have
• Houses or building draws

```html
<!DOCTYPE html>
<html lang="en">
<head>
<meta charset="utf-8">
<title>Lumi Brasa — Business Card</title>
<link href="https://fonts.googleapis.com/css2?family=Open+Sans:wght@400;600;700&display=swap" rel="stylesheet">
<style>
  :root {
    --backdrop: #161616;
    --card: #232323;
    --pink: #e34197;
    --silver: #c4c4c4;
    --text: #e6e6e6;
    --muted: #cfcfcf;
    --rule: #3a3a3a;
  }
  * { margin: 0; padding: 0; box-sizing: border-box; }
  html, body { width: 1200px; height: 900px; overflow: hidden; }
  body {
    background: var(--backdrop);
    font-family: "Open Sans", Arial, sans-serif;
    position: relative;
  }
  .card {
    position: absolute;
    left: 320px;
    width: 560px;
    height: 320px;
    background: var(--card);
    border-radius: 22px;
    box-shadow: 0 14px 30px rgba(0,0,0,.55);
  }
  .card-front { top: 100px; }
  .card-back { top: 480px; }

  .front-logo {
    position: absolute;
    top: 108px; left: 0; right: 0;
    text-align: center;
    font-size: 50px;
    font-weight: 600;
    letter-spacing: 1px;
    color: var(--silver);
  }
  .tagline {
    position: absolute;
    top: 220px; left: 0; right: 0;
    text-align: center;
    font-size: 12px;
    font-weight: 700;
    letter-spacing: .5px;
    color: var(--muted);
  }

  .back-logo {
    position: absolute;
    top: 44px; right: 40px;
    font-size: 46px;
    font-weight: 600;
    color: var(--pink);
    letter-spacing: 1px;
  }
  .back-rule {
    position: absolute;
    top: 124px; left: 240px; right: 36px;
    height: 1px;
    background: var(--rule);
  }
  .holder { position: absolute; left: 40px; top: 168px; }
  .holder-name {
    font-size: 17px;
    font-weight: 700;
    color: var(--pink);
    line-height: 1.1;
  }
  .holder-role { font-size: 15px; color: var(--text); line-height: 1.3; }
  .contacts { list-style: none; margin-top: 8px; }
  .contacts li {
    display: flex; align-items: center; gap: 7px;
    font-size: 15px; color: var(--text); line-height: 21px;
  }
  .contacts svg { width: 12px; height: 12px; fill: var(--pink); flex: none; }
  .address {
    position: absolute;
    right: 40px; top: 200px;
    text-align: right;
    font-size: 14px;
    color: var(--text);
    line-height: 1.35;
  }
</style>
</head>
<body>
  <section class="card card-front">
    <div class="front-logo">Lumi Brasa</div>
    <div class="tagline">THE HOUSE OF YOUR DREAMS!</div>
  </section>

  <section class="card card-back">
    <div class="back-logo">Lumi Brasa</div>
    <div class="back-rule"></div>

    <div class="holder">
      <div class="holder-name">DANIEL MOREIRA</div>
      <div class="holder-role">Managing Director</div>
      <ul class="contacts">
        <li><svg viewBox="0 0 12 12"><path d="M2.5 1 4.5 1 5 3.6 3.8 4.6C4.4 6 5.9 7.5 7.4 8.2L8.4 7 11 7.5 11 9.5C11 10.4 10.2 11 9.4 11 4.8 10.6 1.4 7.2 1 2.6 1 1.8 1.6 1 2.5 1Z"/></svg>(+351) 220 481 356</li>
        <li><svg viewBox="0 0 12 12"><rect x="3" y="1" width="6" height="3"/><rect x="1" y="4.5" width="10" height="4.5" rx="1"/><rect x="3" y="8" width="6" height="3"/></svg>(+351) 220 481 357</li>
        <li><svg viewBox="0 0 12 12"><path d="M1 2.5h10v7H1z M1 2.5 6 6.5 11 2.5" /></svg>geral@lumibrasa.com</li>
        <li><svg viewBox="0 0 12 12"><circle cx="6" cy="6" r="5"/></svg>www.lumibrasa.com</li>
      </ul>
    </div>

    <div class="address">
      Rua das Camélias, 118<br>
      4410-052, Vila Nova de Gaia
    </div>
  </section>
</body>
</html>
```